Meridale Bed Company Needs Business Card

Looking for a very nice looking business card. Creative but not extravagant. We sell beds and pillows across the U.S. and need something professional but catchy. I have attached the logo.

Name : Devin Holt
Title : President
Phone : (800) 471-2960
Email: sleep@quilmora.com
Website: www.quilmora.com

Can be single-sided or double-sided
horizontal or vertical

Can use Blues/Greys

Target Market(s)

Mass Market

Industry/Entity Type

Retail

Contact Information for Business Card

Name : Devin Holt
Title : President
Phone : (800) 471-2960
Email: sleep@quilmora.com
Website: www.quilmora.com

Requirements
Must have
• Clean, Modern, Smooth
• Can use Blues/Greys
• On the other side without the information - have something simple like www.quilmora.com or our logo
Nice to have
• Surprise me
Should not have
• Nothing crazy, nothing cluttered

```html
<!DOCTYPE html>
<html lang="en">
<head>
<meta charset="utf-8">
<title>Quilmora Business Card</title>
<link rel="stylesheet" href="https://fonts.googleapis.com/css2?family=Open+Sans:wght@400;700&display=swap">
<style>
  :root {
    --page-bg: #e6e8eb;
    --card-black: #0d0d0f;
    --card-black-soft: #1c1d20;
    --brand-blue: #35a8dc;
    --swoosh-white: #f2f2f4;
    --text-white: #ffffff;
  }
  html, body {
    margin: 0;
    width: 1200px;
    height: 900px;
    overflow: hidden;
    background: var(--page-bg);
  }
  .sheet {
    position: relative;
    width: 1200px;
    height: 900px;
  }
  .card {
    position: absolute;
    left: 320px;
    width: 560px;
    height: 320px;
    overflow: hidden;
    background: radial-gradient(ellipse at 45% 35%, var(--card-black-soft), var(--card-black) 75%);
    box-shadow: 0 8px 24px rgba(0,0,0,0.22);
  }
  .card--back { top: 100px; }
  .card--front { top: 480px; }
  .wordmark {
    font-family: "Open Sans", sans-serif;
    font-weight: 400;
    color: var(--brand-blue);
    line-height: 1;
    margin: 0;
    position: absolute;
  }
  .card--back .wordmark {
    font-size: 84px;
    left: 0;
    right: 0;
    top: 112px;
    text-align: center;
  }
  .card--front .wordmark {
    font-size: 54px;
    right: 28px;
    top: 40px;
  }
  .wave {
    position: absolute;
    left: 0;
    top: 0;
    width: 560px;
    height: 320px;
  }
  .identity {
    position: absolute;
    left: 44px;
    top: 100px;
    font-family: "Open Sans", sans-serif;
  }
  .identity__name {
    margin: 0;
    font-size: 18px;
    font-weight: 700;
    color: var(--brand-blue);
  }
  .identity__title {
    margin: 2px 0 0 10px;
    font-size: 14px;
    color: var(--text-white);
  }
  .contact {
    position: absolute;
    left: 66px;
    top: 176px;
    margin: 0;
    padding: 0;
    list-style: none;
    font-family: "Open Sans", sans-serif;
    font-size: 15px;
    color: var(--text-white);
  }
  .contact__item {
    display: flex;
    align-items: center;
    gap: 8px;
    height: 22px;
  }
  .contact__icon { width: 13px; height: 11px; fill: var(--brand-blue); }
  .website {
    position: absolute;
    right: 24px;
    top: 198px;
    margin: 0;
    font-family: "Open Sans", sans-serif;
    font-size: 12px;
    color: var(--text-white);
  }
</style>
</head>
<body>
<main class="sheet">
  <section class="card card--back" aria-label="Card back">
    <p class="wordmark">quilmora</p>
  </section>

  <section class="card card--front" aria-label="Card front">
    <svg class="wave" viewBox="0 0 560 320" aria-hidden="true">
      <path d="M0,252 C150,272 300,240 430,176 C320,246 160,286 0,276 Z" fill="var(--swoosh-white)"/>
      <path d="M0,290 C150,300 300,250 400,192 C460,160 520,148 560,146 L560,320 L0,320 Z" fill="var(--brand-blue)"/>
      <path d="M0,288 C150,298 300,248 400,190 C460,158 520,146 560,144" fill="none" stroke="var(--card-black)" stroke-width="3"/>
    </svg>
    <p class="wordmark">quilmora</p>
    <div class="identity">
      <p class="identity__name">Devin Holt</p>
      <p class="identity__title">President</p>
    </div>
    <ul class="contact">
      <li class="contact__item">
        <svg class="contact__icon" viewBox="0 0 13 11" aria-hidden="true"><path d="M1,4 C1,1 12,1 12,4 L10,5 L9,3.5 L4,3.5 L3,5 Z M3,6 L10,6 L11,10 L2,10 Z"/></svg>
        <span>(800) 471-2960</span>
      </li>
      <li class="contact__item">
        <svg class="contact__icon" viewBox="0 0 13 11" aria-hidden="true"><path d="M0,1 L13,1 L6.5,6 Z M0,2.5 L6.5,7.5 L13,2.5 L13,10 L0,10 Z"/></svg>
        <span>sleep@quilmora.com</span>
      </li>
    </ul>
    <p class="website">www.quilmora.com</p>
  </section>
</main>
</body>
</html>
```